QRV Advisors needs a web site

We need a web site for www.qrvadvisors-example.com. QRV is a mergers and acquisition consulting company that focuses our buyer and seller services on logistics companies. We help put companies together, and help with legal and financial due diligence. We want the web site to express our service and show the logistics components. We want personalized images versus pictures of trucks and airplanes.

Our new logo uses Burgandy and grey colors. Image attached. We are not in to bold, big letters...classy, artistic, low key preferred. Confidentiality, experience, professional are what we want to express on the site.

All we expect for the first part of this project is a home page, and one subpage.  We are budgeting other funds for the technical aspects of the web site

Reason: All that I'm seeing so far is trucks, forklifts and planes. We are a legal mergers and acquisitions firm that focus on logistics. I like some of the images to say logistics, but really want it say legal, financial, and putting companies together. Will pay extra for the sub page if someone can impress us with a home page.

Reason: Swamped with another project at the moment...will work on this over the weekend and provide designer feedback and select final design by Tuesday

```html
<!DOCTYPE html>
<html lang="en">
<head>
<meta charset="utf-8">
<title>QRV Advisors — Home</title>
<link href="https://fonts.googleapis.com/css2?family=Ubuntu:wght@400;500;700&family=Open+Sans:wght@400;600&family=Yanone+Kaffeesatz:wght@400&display=swap" rel="stylesheet">
<style>
:root{
  --burgundy:#a3082f;
  --burgundy-dark:#7d0623;
  --grey-text:#444;
  --grey-mid:#6b6b6b;
  --grey-light:#f2f2f2;
  --panel-border:#dcdcdc;
  --footer-bg:#121212;
  --white:#fff;
}
*{box-sizing:border-box;margin:0;padding:0}
html,body{width:1063px;height:1200px;overflow:hidden}
body{position:relative;background:var(--white);font-family:"Open Sans",Arial,sans-serif;color:var(--grey-text)}
.abs{position:absolute}
.top-wash{left:0;top:0;width:1063px;height:407px;background:linear-gradient(#f8f8f8,#e9e9e9)}

.brand{left:141px;top:22px;height:66px;display:flex;align-items:center;gap:12px;font-family:"Ubuntu",sans-serif;font-weight:500;font-size:40px;color:var(--burgundy);letter-spacing:1px;white-space:nowrap}
.brand-mark{width:14px;height:14px;background:var(--burgundy)}
.call{right:143px;top:44px;font-family:"Ubuntu",sans-serif;font-size:18px;color:#555;display:flex;align-items:center;gap:6px}
.call b{font-weight:500;color:#333}

.nav{left:139px;top:105px;width:781px;height:33px;background:var(--burgundy);border:2px solid #d9d9d9;border-radius:3px;display:flex;align-items:center;justify-content:space-between;padding:0 20px 0 10px;font-family:"Ubuntu",sans-serif;font-size:11.6px;font-weight:500;color:var(--white);box-shadow:0 2px 3px rgba(0,0,0,.2)}
.nav .active{background:var(--white);color:var(--grey-mid);padding:5px 12px;border-radius:2px;font-weight:400}

.hero{left:141px;top:155px;width:780px;height:306px;border-radius:4px;background:linear-gradient(170deg,#1d3f8a 0%,#5b7fc0 35%,#c9d6ea 60%,#7f93b5 100%);box-shadow:0 8px 10px -4px rgba(0,0,0,.35);border:3px solid var(--white)}
.hero-title{left:141px;top:180px;width:780px;text-align:center;font-family:"Yanone Kaffeesatz",sans-serif;font-size:26px;line-height:30px;color:var(--white);text-shadow:0 1px 3px rgba(0,0,0,.6)}
.slider-ctrl{left:762px;top:432px;width:105px;height:29px;background:#f4f4f4;border-radius:5px 5px 0 0;display:flex}
.slider-ctrl span{flex:1;display:flex;align-items:center;justify-content:center;border-right:1px solid #ddd}

.panel{background:linear-gradient(#f1f1f1,#fff 40%);border:1px solid var(--panel-border);border-bottom:none;border-radius:3px 3px 0 0}
.panel h2{font-family:"Ubuntu",sans-serif;font-weight:400;font-size:18.5px;color:#555;padding-bottom:6px;border-bottom:2px solid var(--burgundy)}
.panel h2 em{font-style:normal;color:var(--burgundy)}
.welcome{left:139px;top:490px;width:508px;height:186px;padding:8px 12px}
.welcome h2{width:460px}
.welcome p{font-size:10.4px;line-height:15.2px;letter-spacing:.3px;margin-top:10px}
.more{font-size:10.4px;color:var(--burgundy);text-decoration:underline;text-align:right}
.news{left:674px;top:490px;width:249px;height:186px;padding:8px 12px}
.news-item{display:flex;gap:14px;padding:10px 0 10px 2px;border-bottom:1px dotted #4a4aa0}
.date{width:37px;flex:none;text-align:center;font-family:"Ubuntu",sans-serif}
.date .m{background:var(--burgundy);color:var(--white);font-size:10px;padding:2px 0}
.date .d{background:#ddd;color:#333;font-size:14px;font-weight:700;padding:1px 0}
.news-item h3{font-family:"Ubuntu",sans-serif;font-weight:500;font-size:11.5px;color:var(--burgundy)}
.news-item p{font-size:9.6px;color:var(--grey-mid);line-height:13px;margin-top:4px}

.card{top:697px;width:244px}
.card-img{height:133px}
.card-band{height:25px;background:var(--burgundy);display:flex;align-items:center;justify-content:space-between;font-family:"Ubuntu",sans-serif;font-size:15px;font-weight:500;color:var(--white);padding-left:19px;box-shadow:0 6px 6px -4px rgba(0,0,0,.35)}
.card-band span.go{width:33px;height:25px;background:#555;display:flex;align-items:center;justify-content:center}
.card-text{font-size:10.4px;line-height:16.3px;padding:12px 7px 0;height:86px}
.card ul{list-style:none;padding:12px 14px 0;height:86px;font-size:10.4px;line-height:16.3px}
.card li::before{content:"» ";font-size:9px}

.newsletter{left:139px;top:963px;width:784px;height:36px;border:1px solid var(--panel-border);background:#f7f7f7;display:flex;align-items:center}
.nl-tag{height:36px;width:197px;background:var(--burgundy);clip-path:polygon(0 0,93% 0,100% 50%,93% 100%,0 100%);display:flex;align-items:center;gap:8px;padding-left:9px;font-family:"Ubuntu",sans-serif;font-size:16px;font-weight:500;color:var(--white);margin:-1px 0 0 -1px}
.nl-copy{font-size:10px;font-weight:600;color:#333;margin-left:12px}
.nl-field{margin-left:30px;width:163px;height:19px;border:1px solid #bbb;background:#e6e6e6;font-size:10px;color:#555;padding:2px 7px}
.nl-btn{margin-left:9px;height:19px;background:#555;color:var(--white);font-family:"Ubuntu",sans-serif;font-size:11px;font-weight:500;padding:2px 8px}

.footer{left:0;top:1017px;width:1063px;height:183px;background:var(--footer-bg)}
.f-col,.c-row,.follow,.f-brand,.copyright{color:var(--white)}
.f-col h4{font-family:"Ubuntu",sans-serif;font-weight:500;font-size:13.5px;padding-bottom:2px;border-bottom:1px solid #555}
.quick{left:142px;top:1033px;width:88px}
.quick ul{list-style:none;font-size:10.4px;font-weight:600;line-height:17.4px;margin-top:4px;padding-left:2px}
.locations{left:247px;top:1033px;width:178px}
.map{left:247px;top:1057px;width:187px;height:116px;background:linear-gradient(135deg,#e8e4dc,#d9d6cf);border:2px solid #eee}
.contact{left:455px;top:1033px;width:151px}
.c-row{left:452px;display:flex;gap:10px;font-size:11.5px;line-height:14px;align-items:flex-start}
.follow{left:759px;top:1035px;display:flex;align-items:center;gap:8px;font-family:"Ubuntu",sans-serif;font-weight:500;font-size:13.5px}
.follow i{width:24px;height:24px;background:#8a8a8a;border:2px solid #bbb;border-radius:3px;display:block}
.f-brand{left:682px;top:1096px;width:242px;height:36px;display:flex;align-items:center;justify-content:center;gap:10px;font-family:"Ubuntu",sans-serif;font-weight:500;font-size:26px;letter-spacing:1px;white-space:nowrap}
.f-brand i{width:11px;height:11px;background:var(--burgundy);display:block}
.copyright{left:682px;top:1144px;width:242px;text-align:center;font-size:11.5px;line-height:14.5px}
</style>
</head>
<body>
<div class="abs top-wash"></div>

<div class="abs brand"><span class="brand-mark"></span>QRV ADVISORS</div>
<div class="abs call">
  <svg width="20" height="20" viewBox="0 0 20 20"><circle cx="10" cy="10" r="8.5" fill="none" stroke="#a3082f" stroke-width="1.6"/><path d="M7 5.5c-1.5 2.5-1.5 6.5 0 9l1.6-1.2c-.8-2-.8-4.6 0-6.6z" fill="#a3082f"/></svg>
  Call us <b>(012) 555-0147</b>
</div>

<nav class="abs nav">
  <span class="active">HOME</span><span>ABOUT US</span><span>BUYER SERVICES</span><span>SELLER SERVICES</span><span>NEWS &amp; EVENTS</span><span>FAQ's</span><span>CONTACT US</span>
</nav>

<div class="abs hero" role="img" aria-label="Photo of two executives shaking hands in front of office towers and sky"></div>
<div class="abs hero-title">QRV Services Are Offered By<br>Industry Executives With Extensive M&amp;A Experience</div>
<div class="abs slider-ctrl">
  <span><svg width="22" height="10"><path d="M1 1l10 8 10-8" fill="none" stroke="#aaa" stroke-width="1.4"/></svg></span>
  <span style="border:none"><svg width="22" height="10"><path d="M1 9l10-8 10 8" fill="none" stroke="#aaa" stroke-width="1.4"/></svg></span>
</div>

<section class="abs panel welcome">
  <h2>Welcome to QRV <em>Advisors</em></h2>
  <p>QRV assists business owners within the logistics industry to implement growth and exit strategies. We offer business planning and merger and acquisition(M&amp;A) advisory services. QRV services are offered by industry executives with extensive M&amp;A experience. Your company will benefit from a unique and outside perspective from consultants that understand your business.</p>
  <p style="margin-top:18px">QRV can help you formulate and execute your growth strategy. We take a strategic and consultative approach with our advisory services ...</p>
  <div class="more" style="margin-top:4px">Read More »</div>
</section>

<section class="abs panel news">
  <h2>News/Events</h2>
  <div class="news-item"><div class="date"><div class="m">MAR</div><div class="d">29</div></div><div><h3>Duis aute irure reprehenderit</h3><p>Lorem consectetur adipiscing elit. Morbi tristique sem.</p></div></div>
  <div class="news-item"><div class="date"><div class="m">APR</div><div class="d">01</div></div><div><h3>Duis aute irure reprehenderit</h3><p>Lorem consectetur adipiscing elit. Morbi tristique sem.</p></div></div>
  <div class="more" style="margin-top:9px">Read More »</div>
</section>

<article class="abs card" style="left:142px">
  <div class="card-img" role="img" aria-label="Photo of a business team meeting and shaking hands" style="background:linear-gradient(135deg,#e9e6e2,#b9b2aa 60%,#d8d4cf)"></div>
  <div class="card-band">What We Do<span class="go"><svg width="12" height="10"><path d="M0 5h7M5 1l5 4-5 4" fill="none" stroke="#fff" stroke-width="2"/></svg></span></div>
  <p class="card-text">Lorem consectetur adipiscing elit. Morbi tristique sem. Nunc nec ipsum sed nisi Morbi tristique sem.Lorem consectetur adipiscing elit consectetur adi pis cing elit.</p>
  <div class="more">Read More »</div>
</article>

<article class="abs card" style="left:406px">
  <div class="card-img" role="img" aria-label="Photo of consultants discussing documents at a table" style="background:linear-gradient(135deg,#dfe3ea,#8f98a8 55%,#cfd4dc)"></div>
  <div class="card-band">Our Services<span class="go"><svg width="12" height="10"><path d="M0 5h7M5 1l5 4-5 4" fill="none" stroke="#fff" stroke-width="2"/></svg></span></div>
  <ul><li>Business Analysis</li><li>Business Intelligence</li><li>Mergers</li><li>Acquisition</li></ul>
  <div class="more">Read More »</div>
</article>

<article class="abs card" style="left:671px">
  <div class="card-img" role="img" aria-label="Illustration of figures in a maze searching for a goal" style="background:linear-gradient(135deg,#cfcfcf,#7e7e7e 50%,#b5b5b5)"></div>
  <div class="card-band">Our Mission<span class="go"><svg width="12" height="10"><path d="M0 5h7M5 1l5 4-5 4" fill="none" stroke="#fff" stroke-width="2"/></svg></span></div>
  <p class="card-text">Lorem consectetur adipiscing elit. Morbi tristique sem. Nunc nec ipsum sed nisi Morbi tristique sem.Lorem consectetur adipiscing elit consectetur ad ipis cing elit.</p>
  <div class="more">Read More »</div>
</article>

<div class="abs newsletter">
  <div class="nl-tag"><svg width="17" height="17" viewBox="0 0 17 17"><path d="M2 3h8M2 3v12h11v-5" fill="none" stroke="#fff" stroke-width="1.6"/><path d="M7 11l1-3 6-6 2 2-6 6z" fill="#fff"/></svg>Newsletter Signup</div>
  <div class="nl-copy">Lorem ipsum doloronsectetur adipiscing elit. Morbi id tristique.</div>
  <div class="nl-field">Email address</div>
  <div class="nl-btn">SUBMIT</div>
</div>

<footer class="abs footer"></footer>
<div class="abs f-col quick"><h4>Quick Link</h4>
  <ul><li>Home</li><li>About Us</li><li>Buyer Services</li><li>Seller Services</li><li>News &amp; Events</li><li>FAQ's</li><li>Contact us</li></ul>
</div>
<div class="abs f-col locations"><h4>QRV Locations</h4></div>
<div class="abs map" role="img" aria-label="Street map showing the office location"></div>
<div class="abs f-col contact"><h4>Contact Us</h4></div>
<div class="abs c-row" style="top:1063px"><svg width="16" height="14" viewBox="0 0 16 14"><path d="M1 7L8 1l7 6M3 6v7h10V6" fill="none" stroke="#a3082f" stroke-width="1.6"/></svg><span>Lorem consectetur adipiscing<br>elit. Morbi tristique sem.</span></div>
<div class="abs c-row" style="top:1102px"><svg width="16" height="16" viewBox="0 0 16 16"><circle cx="8" cy="8" r="7" fill="none" stroke="#a3082f" stroke-width="1.4"/><path d="M5.5 4.5c-1 2-1 5 0 7l1.3-.9c-.6-1.6-.6-3.6 0-5.2z" fill="#a3082f"/></svg><span>(012) 555-0147</span></div>
<div class="abs c-row" style="top:1130px"><svg width="16" height="14" viewBox="0 0 16 14"><rect x="1" y="5" width="14" height="8" rx="1" fill="#a3082f"/><rect x="4" y="1" width="8" height="5" fill="none" stroke="#a3082f" stroke-width="1.4"/></svg><span>(012) 555-0148</span></div>
<div class="abs c-row" style="top:1159px"><svg width="16" height="12" viewBox="0 0 16 12"><rect x="1" y="1" width="14" height="10" fill="#a3082f"/><path d="M1 1l7 6 7-6" fill="none" stroke="#121212" stroke-width="1.2"/></svg><span>hello@qrvadvisors-example.com</span></div>

<div class="abs follow">Follow Us: <i></i><i></i><i></i></div>
<div class="abs f-brand"><i></i>QRV ADVISORS</div>
<div class="abs copyright">© 2014 QRV ADVISORS.<br>All rights reserved.</div>
</body>
</html>
```